MCLS Banner

We need a design for a pull-up banner (850 x 2000 mm) to promote the Merida Cable Ledger Scheme. https://mclsnet.info/en/
The banner action should be to get people to scan a QR code to join a mailing list (add a frame to add the QR code)

Use the website colours and typology https://mclsnet.info/en/
See also brochure for ideas https://mclsnet.info/documents/9/MCLS_brochure_english.pdf

```html
<!DOCTYPE html>
<html lang="en">
<head>
<meta charset="utf-8">
<title>MCLS Pull-up Banner</title>
<link rel="stylesheet" href="https://fonts.googleapis.com/css2?family=Inter:wght@400;500;600;700;800&display=swap">
<style>
  :root {
    --navy: #11112a;
    --lime: #bcd232;
    --white: #ffffff;
    --blue: #3a8fd4;
    --ink: #15152a;
    --backdrop: #efefef;
    --map-green: #c9dfb0;
    --map-light: #ece9df;
  }
  * { box-sizing: border-box; margin: 0; padding: 0; }
  html, body { width: 1200px; height: 1137px; overflow: hidden; }
  body {
    background: var(--backdrop);
    font-family: "Inter", Arial, sans-serif;
    position: relative;
  }
  .banner {
    position: absolute;
    left: 410px; top: 95px;
    width: 406px; height: 959px;
    background: var(--white);
    box-shadow: 0 2px 6px rgba(0,0,0,0.12);
    overflow: hidden;
  }
  .hero {
    position: absolute; left: 0; top: 0;
    width: 100%; height: 355px;
    background: var(--navy);
    color: var(--white);
  }
  .brand-name {
    position: absolute; left: 36px; top: 34px;
    font-size: 112px; font-weight: 600;
    letter-spacing: -3px; line-height: 1;
    color: var(--white);
  }
  .headline {
    position: absolute; left: 40px; top: 162px;
    font-size: 30px; font-weight: 700; line-height: 36px;
    letter-spacing: 0.2px;
  }
  .headline-rule {
    position: absolute; left: 40px; top: 279px;
    width: 240px; height: 2px; background: var(--white);
  }
  .standard-name {
    position: absolute; left: 40px; top: 292px;
    font-size: 18px; font-weight: 400; letter-spacing: 0.4px;
  }
  .accent-band {
    position: absolute; left: 0; top: 355px;
    width: 100%; height: 17px; background: var(--lime);
  }
  .taglines {
    position: absolute; left: 32px; top: 446px;
    color: var(--blue);
    font-size: 22px; font-weight: 700; line-height: 27px;
    list-style: none;
  }
  .taglines li { margin-bottom: 7px; }
  .taglines li:last-child { margin-bottom: 0; }
  .network-map {
    position: absolute; left: 210px; top: 398px;
    width: 174px; height: 164px;
    background: linear-gradient(135deg, var(--map-green) 0%, var(--map-light) 45%, var(--map-green) 100%);
  }
  .benefits {
    position: absolute; left: 96px; top: 606px;
    list-style: none;
    color: var(--ink);
    font-size: 14px; font-weight: 500; line-height: 16px;
  }
  .benefits li {
    display: flex; align-items: flex-start; gap: 14px;
    margin-bottom: 16px;
  }
  .benefits li:nth-child(2) { margin-bottom: 16px; }
  .benefits svg { flex: none; width: 20px; height: 20px; margin-top: -1px; }
  .cta-band {
    position: absolute; left: 0; top: 765px;
    width: 100%; height: 59px;
    background: var(--lime);
    color: var(--ink);
    font-size: 21px; font-weight: 600;
    padding-left: 36px;
    display: flex; align-items: center;
  }
  .signup {
    position: absolute; left: 0; top: 824px;
    width: 100%; height: 135px;
    background: var(--navy);
  }
  .qr-frame {
    position: absolute; left: 37px; top: 23px;
    width: 93px; height: 93px;
    background: var(--white); border-radius: 4px;
  }
  .signup-text {
    position: absolute; left: 168px; top: 28px;
    color: var(--white);
    font-size: 12.5px; line-height: 14.5px; letter-spacing: 0.2px;
  }
  .signup-rule {
    position: absolute; left: 168px; top: 81px;
    width: 132px; height: 1px; background: var(--white);
  }
  .signup-url {
    position: absolute; left: 168px; top: 91px;
    color: var(--lime);
    font-size: 16px; font-weight: 500; letter-spacing: 0.4px;
  }
</style>
</head>
<body>
  <main class="banner">
    <section class="hero">
      <div class="brand-name">mcls</div>
      <h1 class="headline">Mapping the<br>world’s internet<br>backbone</h1>
      <div class="headline-rule"></div>
      <p class="standard-name">Merida Cable Ledger Scheme</p>
    </section>
    <div class="accent-band"></div>

    <ul class="taglines">
      <li>Standardize.</li>
      <li>Share.</li>
      <li>Strengthen<br>connectivity.</li>
    </ul>

    <div class="network-map" role="img" aria-label="Map of fibre network spans and nodes coloured by status, with a legend"></div>

    <ul class="benefits">
      <li>
        <svg viewBox="0 0 20 20" aria-hidden="true"><circle cx="10" cy="10" r="8.5" fill="none" stroke="#15152a" stroke-width="1.8"/><path d="M6 10.2l2.8 2.8L14 7.6" fill="none" stroke="#15152a" stroke-width="1.8" stroke-linecap="round" stroke-linejoin="round"/></svg>
        <span>Improve fibre<br>network transparency</span>
      </li>
      <li>
        <svg viewBox="0 0 20 20" aria-hidden="true"><circle cx="10" cy="10" r="8.5" fill="none" stroke="#15152a" stroke-width="1.8"/><path d="M6 10.2l2.8 2.8L14 7.6" fill="none" stroke="#15152a" stroke-width="1.8" stroke-linecap="round" stroke-linejoin="round"/></svg>
        <span>Support better infrastructure planning</span>
      </li>
      <li>
        <svg viewBox="0 0 20 20" aria-hidden="true"><circle cx="10" cy="10" r="8.5" fill="none" stroke="#15152a" stroke-width="1.8"/><path d="M6 10.2l2.8 2.8L14 7.6" fill="none" stroke="#15152a" stroke-width="1.8" stroke-linecap="round" stroke-linejoin="round"/></svg>
        <span>Enable collaboration across operators,<br>regulators &amp; researchers</span>
      </li>
    </ul>

    <div class="cta-band">Join the MCLS Mailing List</div>

    <section class="signup">
      <div class="qr-frame" aria-label="Space for mailing list QR code"></div>
      <p class="signup-text">To stay update with and<br>contribute to the development<br>and adoption of MCLS</p>
      <div class="signup-rule"></div>
      <p class="signup-url">www.mclsnet.info</p>
    </section>
  </main>
</body>
</html>
```